Wesbite design for Investment Firm

We want a basic (clean) website that follows the form, fonts and colors of our attachments. This is for a financial investment management firm, but we have a boutique (anti-Wall Street) approach. Site should have an Home Page (Logo up top - room for basic copy on bottom, Philosophy Page (room for Quarterly Letter attachment and basic copy, Performance Page (room for Performance Overview and Performance Analysis and basic copy), Team Page, Commentary Page and Contact

Reason: Some designers have asked for an extension. Again, please only use image of Train Station or Train Station Logo in design.

Target Market(s)

Small and mid-size financial advisors from across the country

Industry/Entity Type

Financial

Number of Pages Required

5+ page

Font styles to use
Other font styles liked:
• Palotino Linotype

Colors
3176b5
cfdeed
ffffff

Requirements
Must have
• Please refer to existing site www.qlvor.example. Of note, this is too complex / cluttered. We simply want Blur, Grey and White consistent with attachments. The copy is pretty good, but will be simplified (and no quotes)
Should not have
• No images other than train station logo and / or train station image

```html
<!DOCTYPE html>
<html lang="en">
<head>
<meta charset="utf-8">
<title>Ashgrove Investment Company</title>
<link href="https://fonts.googleapis.com/css2?family=Crimson+Pro:wght@400;500&family=Tinos&display=swap" rel="stylesheet">
<style>
  :root {
    --navy: #0d2a5c;
    --ink: #1a1a1a;
    --body-grey: #555555;
    --rule: #d9d9d9;
    --sketch-dark: #cfcfcf;
    --sketch-mid: #e0e0e0;
    --sketch-light: #f1f1f1;
    --white: #ffffff;
  }
  * { margin: 0; padding: 0; box-sizing: border-box; }
  html, body { width: 1200px; height: 843px; overflow: hidden; background: var(--white); }
  body { position: relative; font-family: "Crimson Pro", "Palatino Linotype", serif; }

  .site-header {
    position: absolute; top: 0; left: 0; width: 1200px; height: 67px;
    background: var(--white);
    box-shadow: 0 1px 3px rgba(0,0,0,0.18);
    border-bottom: 1px solid #cfcfcf;
    z-index: 2;
  }
  .brand {
    position: absolute; left: 101px; top: 19px;
    font-family: "Crimson Pro", serif; font-weight: 500;
    font-size: 25px; color: var(--navy); line-height: 1;
  }
  .main-nav a {
    position: absolute; top: 32px; font-size: 18px; color: var(--ink);
    text-decoration: none; white-space: nowrap; line-height: 1;
  }

  .hero-sketch {
    position: absolute; left: 107px; top: 67px; width: 1012px; height: 540px;
    border-radius: 0 0 50% 50% / 0 0 38% 38%;
    background:
      radial-gradient(ellipse 42% 52% at 66% 42%, var(--sketch-dark) 0%, rgba(207,207,207,0) 100%),
      radial-gradient(ellipse 30% 40% at 24% 58%, rgba(210,210,210,0.8) 0%, rgba(210,210,210,0) 100%),
      radial-gradient(ellipse 52% 58% at 50% 44%, var(--sketch-mid) 0%, var(--sketch-light) 70%, rgba(255,255,255,0) 100%);
    z-index: 0;
  }

  .intro {
    position: absolute; left: 150px; top: 598px; width: 900px;
    text-align: center; z-index: 1;
  }
  .intro h1 { font-weight: 400; font-size: 27px; color: var(--navy); line-height: 1.2; }
  .intro p {
    font-family: "Tinos", "Times New Roman", serif;
    font-size: 14.6px; line-height: 23px; color: var(--body-grey);
    margin-top: 16px;
  }
  .intro h1 + p { margin-top: 19px; }

  .footer-rule {
    position: absolute; left: 96px; top: 790px; width: 1007px;
    border: 0; border-top: 1px solid var(--rule);
  }
  .site-footer {
    position: absolute; top: 805px; left: 0; width: 1200px;
    text-align: center; font-size: 17px; color: var(--navy);
  }
</style>
</head>
<body>
  <header class="site-header">
    <div class="brand">Ashgrove Investment Company</div>
    <nav class="main-nav">
      <a href="#" style="left:579px">Our Philosophy</a>
      <a href="#" style="left:717px">Performance</a>
      <a href="#" style="left:833px">Our Team</a>
      <a href="#" style="left:930px">Commentary</a>
      <a href="#" style="left:1046px">Contact</a>
    </nav>
  </header>

  <div class="hero-sketch" role="img" aria-label="Pencil sketch of a historic train station with a locomotive, tracks and iron fence, fading softly into white"></div>

  <section class="intro">
    <h1>We Are A Financial Investment Management Firm With A Boutique Approach.</h1>
    <p>We founded Ashgrove Investment Company in 1999, initially managing wealth from our family and friends in the town of Ashgrove. The high expectations of our original investors is a key contributor to our value driven investment philosophy.</p>
    <p>Based in Dallas, TX, we manage assets for both individuals and institutions. Our investment methodology stresses absolute returns vs. relative performance, blending a combination of fundamental analysis, discipline and patience with the goal of preserving and compounding capital</p>
  </section>

  <hr class="footer-rule">
  <footer class="site-footer">Copyright © 2017&nbsp; Ashgrove Investment Company.&nbsp; All Right Reserved.</footer>
</body>
</html>
```